Business Card Design

Buy and sell properties
Buy and rehab properties
Buy properties for cash
That is what I do but do need a logo
looking for some type of logo or design on it
Just started business
Back of card should say something like BUY HOUSES CASH
Overview: it is a new company. Basically I buy properties wholesale and fix them up and sell them or sell them to other fix and flippers
Background: company is new so not any background
Market: is basically anyone selling a house or buying a house. Someone that needs to sell house fast. Basically I am a cash home buyer!!!

Updates
Email on card should be:   harborlanerealtyinc@mailnest.com

Industry/Entity Type
House
Contact Information for Business Card
Harbor Lane Realty Inc
PO Box 718296
Coral Mill Key FL 33071

Dwight Kallum
harborlanerealtyinc@mailnest.com
305-271-5589

```html
<!DOCTYPE html>
<html lang="en">
<head>
<meta charset="utf-8">
<title>Harbor Lane Realty Inc — Business Card</title>
<link href="https://fonts.googleapis.com/css2?family=Arimo:wght@400;700&display=swap" rel="stylesheet">
<style>
  :root {
    --canvas: #ffffff;
    --frame: #d4d4d4;
    --card-dark: #000000;
    --card-light: #ffffff;
    --card-border: #9a9a9a;
    --ink-light: #ffffff;
    --ink-gray: #5a5a5a;
    --ink-dark: #333333;
    --mark-gray: #5f5f5f;
  }
  html, body {
    margin: 0;
    padding: 0;
    width: 1200px;
    height: 1000px;
    overflow: hidden;
    background: var(--canvas);
    font-family: "Arimo", Arial, sans-serif;
  }
  .stage {
    position: relative;
    width: 1198px;
    height: 998px;
    border: 1px solid var(--frame);
    background: var(--canvas);
  }
  .card {
    position: absolute;
    box-sizing: border-box;
  }
  .card--front {
    left: 359px;
    top: 181px;
    width: 488px;
    height: 279px;
    background: var(--card-dark);
  }
  .card--back {
    left: 355px;
    top: 547px;
    width: 489px;
    height: 279px;
    background: var(--card-light);
    border: 1px solid var(--card-border);
  }
  .brand-dot {
    position: absolute;
    border-radius: 50%;
  }
  .card--front .brand-dot {
    left: 204px;
    top: 58px;
    width: 80px;
    height: 80px;
    background: var(--ink-light);
  }
  .card--front .brand-name {
    position: absolute;
    left: 0;
    right: 0;
    top: 162px;
    text-align: center;
    color: var(--ink-light);
    font-weight: 700;
    font-size: 31px;
    letter-spacing: 0.3px;
    margin: 0;
  }
  .card--back .brand-dot {
    left: 74px;
    top: 93px;
    width: 58px;
    height: 58px;
    background: var(--mark-gray);
  }
  .card--back .brand-name {
    position: absolute;
    left: 8px;
    width: 190px;
    top: 164px;
    text-align: center;
    color: var(--ink-dark);
    font-weight: 700;
    font-size: 13.5px;
    margin: 0;
  }
  .divider {
    position: absolute;
    left: 196px;
    top: 46px;
    width: 2px;
    height: 192px;
  }
  .contact {
    position: absolute;
    left: 226px;
    top: 76px;
    color: var(--ink-gray);
  }
  .contact__name {
    margin: 0 0 22px;
    font-size: 32px;
    font-weight: 700;
    letter-spacing: 0.5px;
    line-height: 1;
  }
  .contact__line {
    margin: 0;
    font-size: 16px;
    font-weight: 700;
    letter-spacing: 1.2px;
    line-height: 23px;
  }
  .contact__line--email {
    font-size: 12.5px;
    letter-spacing: 0.3px;
  }
</style>
</head>
<body>
  <main class="stage">
    <section class="card card--front" aria-label="Card front">
      <div class="brand-dot"></div>
      <h1 class="brand-name">Harbor Lane Realty Inc</h1>
    </section>

    <section class="card card--back" aria-label="Card back">
      <div class="brand-dot"></div>
      <p class="brand-name">Harbor Lane Realty Inc</p>
      <svg class="divider" viewBox="0 0 2 192" preserveAspectRatio="none" aria-hidden="true">
        <defs>
          <linearGradient id="dividerFade" x1="0" y1="0" x2="0" y2="1">
            <stop offset="0" stop-color="#9a9a9a" stop-opacity="0.3"/>
            <stop offset="0.5" stop-color="#7a7a7a"/>
            <stop offset="1" stop-color="#9a9a9a" stop-opacity="0.3"/>
          </linearGradient>
        </defs>
        <rect width="2" height="192" fill="url(#dividerFade)"/>
      </svg>
      <div class="contact">
        <p class="contact__name">Dwight Kallum</p>
        <p class="contact__line">305-271-5589</p>
        <p class="contact__line">PO Box 718296</p>
        <p class="contact__line">Coral Mill Key FL 33071</p>
        <p class="contact__line contact__line--email">harborlanerealtyinc@mailnest.com</p>
      </div>
    </section>
  </main>
</body>
</html>
```